Website for new slot-booking/reservations website/software

For a new software product we need a brand new logo and website for a reservations/booking system. The website should ideally present the main features with information text, contact info, news page as well as registration and pricing pages. As currently primary field of operation the software should be used for tennis but later on, also for other sport types. Also we'd like to be the logo a text-brand which includes the name "zeitfeldo.com" or just "zeitfeldo". The logo should ideally include an icon-design in some way. Generally we are open for ideas.

Bootstrap 4 template is a minimum requirement. (Multi-Page preferred, Single-Page still OK.)

You can use the attached image as an inspiration, but change of colors or other design elements are up to you. Currently the application has a primary color of #5500ff. The website created by you will not include the application itself, so it can have different (but ideally similar) Look&Feel.
Updates

Target Market(s)

Sports, Club-Management

Logo Text

zeitfeldo.com

Coding

Coded - Design and coding required

Number of Pages Required

5+ page

Font styles to use
Sans Serif

Requirements
Must have
• Bootstrap 4 Template, SCSS
Nice to have
• Rapid Loading Times, not too much external JS Libraries.
Should not have
• Extensive animations

```html
<!DOCTYPE html>
<html lang="en">
<head>
<meta charset="utf-8">
<title>Zeitfeldo – Slot-Booking Reservations</title>
<link rel="stylesheet" href="https://fonts.googleapis.com/css2?family=Roboto:wght@400;500;700;900&family=Lato:ital,wght@0,400;0,700;1,400&family=Poppins:wght@300;400;500&display=swap">
<style>
:root{
  --primary:#4a00f0;
  --teal:#1fa88f;
  --ink:#1d1d1d;
  --muted:#8a8a8a;
  --text:#333;
  --card:#f0eeef;
  --white:#fff;
}
*{margin:0;padding:0;box-sizing:border-box}
html,body{width:1200px;height:2546px;overflow:hidden}
body{position:relative;background:var(--white);font-family:"Lato",sans-serif;color:var(--text)}
.abs{position:absolute}

/* header */
.site-header{top:0;left:0;width:1200px;height:76px;background:var(--white)}
.brand{left:143px;top:24px;display:flex;align-items:center;gap:10px;font-family:"Roboto",sans-serif;font-weight:700;font-size:22px;color:var(--primary);text-transform:uppercase}
.brand-dot{width:24px;height:24px;border-radius:50%;background:var(--primary)}
.main-nav{right:134px;top:28px;display:flex;gap:25px;font-family:"Roboto",sans-serif;font-weight:500;font-size:15px;color:var(--ink)}
.main-nav .active{color:var(--primary)}

/* hero */
.hero{top:76px;left:0;width:1200px;height:473px;
  background:
    radial-gradient(ellipse 220px 260px at 390px 180px,rgba(20,10,90,.28),transparent 70%),
    radial-gradient(ellipse 200px 200px at 820px 120px,rgba(10,60,80,.22),transparent 70%),
    radial-gradient(ellipse 180px 220px at 1080px 260px,rgba(10,80,70,.2),transparent 70%),
    linear-gradient(100deg,var(--primary) 0%,#3a2ae0 40%,#2a80b8 70%,var(--teal) 100%)}
.hero-title{right:671px;top:234px;text-align:right;font-family:"Roboto",sans-serif;font-weight:900;font-size:40px;line-height:45px;color:var(--white);text-transform:uppercase}
.btn-learn{left:408px;top:382px;width:120px;height:35px;background:var(--white);border-radius:2px;box-shadow:0 3px 6px rgba(0,0,0,.3);font-family:"Roboto",sans-serif;font-weight:700;font-size:11px;color:var(--primary);display:flex;align-items:center;justify-content:center;text-transform:uppercase}
.slider-dots{left:469px;top:441px;display:flex;gap:5px}
.slider-dots span{width:11px;height:11px;border:1.5px solid var(--white);border-radius:50%}
.slider-dots span.on{background:var(--primary)}
.app-preview{left:546px;top:198px;width:630px;height:380px;border-radius:10px;background:linear-gradient(180deg,#d8d6f2 0%,#eceaf6 70%,#d9d9dd 100%)}

/* what we do */
.section-title{left:0;width:1200px;text-align:center;font-family:"Poppins",sans-serif;font-weight:300;font-size:26px;line-height:38px;letter-spacing:17px;color:var(--primary);text-transform:uppercase}
.section-lead{left:280px;width:640px;top:680px;text-align:center;font-size:15.5px;line-height:25px;color:var(--muted)}
.feature{width:240px;text-align:center}
.feature-icon{position:relative;width:120px;height:120px;margin:0 auto;border-radius:50%;border:2px solid var(--primary);display:flex;align-items:center;justify-content:center}
.feature-num{position:absolute;right:-12px;top:4px;width:36px;height:36px;border-radius:50%;background:linear-gradient(135deg,var(--primary),var(--teal));color:#fff;font-family:"Poppins",sans-serif;font-size:15px;display:flex;align-items:center;justify-content:center}
.feature h3{margin-top:28px;font-size:19px;font-weight:700;color:var(--ink)}
.feature p{margin-top:14px;font-size:14.5px;line-height:22px;color:var(--text)}

/* cta band */
.cta-band{top:1143px;left:0;width:1200px;height:483px;
  background:
    radial-gradient(ellipse 260px 200px at 300px 300px,rgba(10,60,60,.22),transparent 70%),
    radial-gradient(ellipse 200px 180px at 700px 160px,rgba(20,20,90,.22),transparent 70%),
    linear-gradient(90deg,var(--teal) 0%,#1e70c0 40%,#3a10e6 72%,var(--primary) 100%)}
.cta-text{left:0;width:1200px;top:1278px;text-align:center;font-family:"Roboto",sans-serif;font-weight:700;font-size:32px;line-height:45px;color:var(--white)}
.play-btn{left:566px;top:1413px;width:68px;height:68px}

/* testimonials */
.testimonial{left:191px;top:1762px;width:818px;height:283px;background:var(--card);border:1px solid #dcdcdc;box-shadow:0 8px 16px rgba(40,140,200,.18)}
.quote{left:300px;top:1811px;width:600px;text-align:center;font-style:italic;font-size:20px;line-height:30px;color:var(--ink);white-space:nowrap}
.quote-mark{font-family:"Poppins",sans-serif;font-style:normal;font-weight:500;font-size:26px;color:var(--teal)}
.quote-author{left:0;width:1200px;top:1964px;text-align:center;font-size:15.5px;color:var(--primary)}
.nav-arrow{width:34px;height:34px;border-radius:50%;top:1887px}
.nav-arrow.prev{left:177px;background:var(--teal)}
.nav-arrow.next{left:989px;background:var(--primary)}

/* footer */
.site-footer{top:2148px;left:0;width:1200px;height:325px;
  background:
    radial-gradient(ellipse 160px 140px at 220px 100px,rgba(200,170,150,.18),transparent 70%),
    radial-gradient(ellipse 200px 160px at 820px 90px,rgba(210,150,110,.18),transparent 70%),
    linear-gradient(180deg,#f4f4f6 0%,#eceaee 60%,#e4ece2 100%);border-top:1px solid #ddd}
.footer-brand{left:142px;top:2266px;width:200px;text-align:center;font-family:"Roboto",sans-serif;font-weight:700;font-size:22px;color:var(--primary);text-transform:uppercase}
.footer-mark{left:227px;top:2214px;width:32px;height:32px;border-radius:50%;background:var(--primary)}
.social{left:179px;top:2305px;display:flex;gap:3px}
.social span{width:30px;height:30px;border-radius:50%;border:1.5px solid #444}
.footer-col h4{font-family:"Poppins",sans-serif;font-weight:500;font-size:18px;color:#2a2a2a;text-transform:uppercase;letter-spacing:.3px}
.footer-col p,.footer-col li{font-family:"Poppins",sans-serif;font-size:13.5px;color:#444}
.newsletter-input{width:274px;height:40px;border:1px solid #ccc;border-radius:20px;background:#fff;padding-left:14px;display:flex;align-items:center;font-family:"Poppins",sans-serif;font-size:11px;color:#444}
.btn-signup{width:115px;height:35px;border-radius:18px;background:linear-gradient(90deg,var(--teal),var(--primary));color:#fff;font-family:"Poppins",sans-serif;font-weight:500;font-size:15px;display:flex;align-items:center;justify-content:center;text-transform:uppercase}
.contact-row{display:flex;gap:14px;align-items:flex-start}
.contact-row svg{flex:none;margin-top:3px}
.quick-links{list-style:none}
.quick-links li{height:27.5px;font-size:14px}
.footer-bar{top:2473px;left:0;width:1200px;height:73px;background:var(--primary);color:#fff;font-size:14px;display:flex;align-items:center;justify-content:center}
</style>
</head>
<body>

<header class="site-header abs">
  <div class="brand abs"><span class="brand-dot"></span>zeitfeldo</div>
  <nav class="main-nav abs">
    <span class="active">Home</span><span>News &amp; Events</span><span>Our Portfolio</span><span>Our Capabilities</span><span>Investors</span><span>Contact</span>
  </nav>
</header>

<section class="hero abs" role="img" aria-label="Sports photo montage of athletes tinted in a violet to teal gradient"></section>
<h1 class="hero-title abs">zeitfeldo<br>Slot-Booking<br>Reservations</h1>
<a class="btn-learn abs">Learn More</a>
<div class="slider-dots abs"><span class="on"></span><span></span><span></span><span></span></div>
<div class="app-preview abs" role="img" aria-label="Photo of a laptop showing the members list of the booking application"></div>

<h2 class="section-title abs" style="top:636px">What we do</h2>
<p class="section-lead abs">Sed ut perspiciatis unde omnis iste natus error sit voluptatem accusantium doloremque laudantium, totam rem aperiam, eaque ipsa quae ab illo</p>

<div class="feature abs" style="left:138px;top:760px">
  <div class="feature-icon">
    <svg width="54" height="46" viewBox="0 0 54 46" fill="none" stroke="#555" stroke-width="2"><rect x="2" y="2" width="50" height="42"/><line x1="2" y1="12" x2="52" y2="12"/><path d="M34 36l5 5 9-10"/></svg>
    <span class="feature-num">01</span>
  </div>
  <h3>Nemo enim ipsam</h3>
  <p>Sed ut perspiciatis unde omnis iste natus sit voluptatem accusantium doloremque laudantium, totam rem aperiam, eaque ipsa</p>
</div>
<div class="feature abs" style="left:476px;top:800px">
  <div class="feature-icon">
    <svg width="46" height="54" viewBox="0 0 46 54"><defs><linearGradient id="docg" x1="0" y1="0" x2="0" y2="1"><stop offset="0" stop-color="#4a00f0"/><stop offset="1" stop-color="#1fa88f"/></linearGradient></defs><rect x="2" y="2" width="32" height="50" fill="url(#docg)"/><rect x="26" y="2" width="18" height="14" fill="#4a00f0"/><path d="M31 7h8l-4 5z" fill="#fff"/><g stroke="#fff" stroke-width="3"><line x1="8" y1="20" x2="28" y2="20"/><line x1="8" y1="28" x2="28" y2="28"/><line x1="8" y1="36" x2="28" y2="36"/><line x1="8" y1="44" x2="28" y2="44"/></g></svg>
    <span class="feature-num">02</span>
  </div>
  <h3>Nemo enim ipsam</h3>
  <p>Sed ut perspiciatis unde omnis iste natus sit voluptatem accusantium doloremque laudantium, totam rem aperiam, eaque ipsa</p>
</div>
<div class="feature abs" style="left:814px;top:760px">
  <div class="feature-icon">
    <svg width="52" height="44" viewBox="0 0 52 44" fill="none" stroke="#555" stroke-width="2" stroke-linejoin="round"><path d="M2 22L50 2 38 42 26 28z"/><path d="M50 2L26 28v14l6-10"/></svg>
    <span class="feature-num">03</span>
  </div>
  <h3>Nemo enim ipsam</h3>
  <p>Sed ut perspiciatis unde omnis iste natus sit voluptatem accusantium doloremque laudantium, totam rem aperiam, eaque ipsa</p>
</div>

<section class="cta-band abs" role="img" aria-label="Faded photo of football and rugby players behind a teal to violet gradient"></section>
<p class="cta-text abs">Can you help translate this site into a foreign language ?<br>Please email us with details if you can help.</p>
<svg class="play-btn abs" viewBox="0 0 68 68"><circle cx="34" cy="34" r="32" fill="#fff" stroke="#fff" stroke-width="2"/><circle cx="34" cy="34" r="28" fill="none" stroke="#2a6fd0" stroke-width="2"/><path d="M28 22l16 12-16 12z" fill="#1e3fd0"/></svg>

<h2 class="section-title abs" style="top:1696px">Our clients say</h2>
<div class="testimonial abs"></div>
<p class="quote abs"><span class="quote-mark">“</span>&nbsp;&nbsp;Sed ut perspiciatis unde omnis iste natus error sit voluptatem<br>accusantium doloremque laudantium, totam rem aperiam, eaque ipsa<br>quae ab illo inventore veritatis et quasi architecto beatae vitae dicta<br>sunt explicabo.&nbsp;&nbsp;&nbsp;&nbsp;&nbsp;&nbsp;&nbsp;&nbsp;&nbsp;&nbsp;&nbsp;&nbsp;<span class="quote-mark">”</span></p>
<p class="quote-author abs">Martin, Nordlicht Studio</p>
<svg class="nav-arrow prev abs" viewBox="0 0 34 34"><path d="M19 11l-6 6 6 6" stroke="#fff" stroke-width="2" fill="none"/></svg>
<svg class="nav-arrow next abs" viewBox="0 0 34 34"><path d="M15 11l6 6-6 6" stroke="#fff" stroke-width="2" fill="none"/></svg>

<footer class="site-footer abs" role="img" aria-label="Faint photo of sports balls on grass"></footer>
<div class="footer-mark abs"></div>
<div class="footer-brand abs">zeitfeldo</div>
<div class="social abs"><span></span><span></span><span></span><span></span></div>

<div class="footer-col abs" style="left:384px;top:2205px;width:280px">
  <h4>Sign up for newsletter</h4>
  <p style="margin-top:26px;font-size:12.5px;line-height:20px">Excepteur sint occaecat cupidatat non proident, sunt in culpa qui officia deserunt</p>
  <div class="newsletter-input" style="margin-top:12px">Enter email</div>
  <div class="btn-signup" style="margin-top:14px">Sign Up</div>
</div>

<div class="footer-col abs" style="left:686px;top:2205px;width:240px">
  <h4>Contact us</h4>
  <div class="contact-row" style="margin-top:32px">
    <svg width="16" height="20" viewBox="0 0 16 20"><path d="M8 0a8 8 0 0 1 8 8c0 6-8 12-8 12S0 14 0 8a8 8 0 0 1 8-8z" fill="#1f70c8"/><circle cx="8" cy="8" r="3" fill="#fff"/></svg>
    <p style="line-height:22px">1417 Larkspur Lane<br>Cedar Hollow, Oregon</p>
  </div>
  <div class="contact-row" style="margin-top:6px">
    <svg width="18" height="18" viewBox="0 0 18 18"><path d="M4 1l3 4-2 2a10 10 0 0 0 6 6l2-2 4 3-2 3C8 17 1 10 1 3z" fill="#1f70c8"/></svg>
    <p style="line-height:20px">Phone:<br>541-306-2278</p>
  </div>
  <div class="contact-row" style="margin-top:12px">
    <svg width="18" height="14" viewBox="0 0 18 14"><rect width="18" height="14" fill="#1f70c8"/><path d="M0 0l9 7 9-7" stroke="#fff" stroke-width="1.5" fill="none"/></svg>
    <p style="line-height:20px">Email:<br>info@zeitfeldo.com</p>
  </div>
</div>

<div class="footer-col abs" style="left:937px;top:2205px;width:160px">
  <h4>Quick links</h4>
  <ul class="quick-links" style="margin-top:18px;padding-left:4px">
    <li>Home</li><li>News &amp; Events</li><li>Our Portfolio</li><li>Our Capabilities</li><li>Investors</li><li>Contact</li>
  </ul>
</div>

<div class="footer-bar abs">zeitfeldo © 2021 All Rights Reserved | Privacy Policy | Terms and Conditions</div>

</body>
</html>
```